Report template for evaluation reports to be used by non designers

We are looking for a report template that meets all the requirements listed in the attached documents. letter head, logo etc have been enclosed. Its important that the colour integrity is kept, but beyond that options are welcome.
Its important that the document is extremely easy to use and that is able to be adapted to include eatables, figures, pictures, text boxes etc and keep the integrity of the template

Target Market(s)

Governments, Civil society organisations and research institutions

Font styles to use
Sans Serif

Colors
6b449b
876aae
c0c0c0
000000

Requirements
Must have
• Clean, professional, not concluded, modern, must be easy to use
Should not have
• too busy, hard to use

```html
<!DOCTYPE html>
<html lang="en">
<head>
<meta charset="utf-8">
<title>Civic Analysis Institute – Report Covers</title>
<link rel="stylesheet" href="https://fonts.googleapis.com/css2?family=Open+Sans:wght@400;600;700&display=swap">
<style>
  :root {
    --purple: #5b4a9c;
    --purple-deep: #6b449b;
    --purple-soft: #876aae;
    --silver: #c0c0c0;
    --ink: #000000;
    --paper: #f1f1f3;
    --backdrop: #a3a3a5;
    --white: #ffffff;
    --photo-light: #dfe3ea;
    --photo-dark: #8a8f99;
  }
  * { box-sizing: border-box; margin: 0; padding: 0; }
  html, body { width: 1200px; height: 925px; overflow: hidden; }
  body {
    background: var(--backdrop);
    font-family: "Open Sans", sans-serif;
    color: var(--ink);
  }
  .spread {
    position: absolute;
    left: 80px; top: 95px;
    width: 1040px; height: 735px;
    display: flex;
  }
  .page {
    position: relative;
    width: 520px; height: 735px;
    background: var(--paper);
    overflow: hidden;
  }
  .page--back { border-right: 1px solid #dcdce0; }

  /* Brand name */
  .brand {
    position: absolute; top: 42px; left: 0; right: 0;
    text-align: center;
  }
  .brand__name {
    font-size: 38px; font-weight: 400; letter-spacing: 10px;
    color: var(--ink); line-height: 1;
  }
  .brand__sub {
    margin-top: 6px;
    font-size: 10px; font-weight: 600; letter-spacing: 4px;
    color: var(--purple);
  }

  /* Cover image area */
  .cover-photo {
    position: absolute; left: 40px; top: 118px;
    width: 480px; height: 270px;
    background: linear-gradient(135deg, var(--photo-light) 0%, #c9ced8 45%, var(--photo-dark) 100%);
  }

  /* Purple bands */
  .band { position: absolute; }
  .band svg { display: block; width: 100%; height: 100%; }
  .band__text {
    position: absolute; inset: 0;
    display: flex; align-items: center;
    color: var(--white); font-weight: 700;
  }
  .band--title { left: 120px; top: 300px; width: 400px; height: 210px; }
  .band--title .band__text {
    padding: 0 30px 0 60px;
    font-size: 30px; line-height: 1.15;
  }
  .band--thanks { left: 0; top: 330px; width: 520px; height: 170px; }
  .band--thanks .band__text {
    justify-content: center; padding-left: 40px;
    font-size: 46px;
  }

  /* Details */
  .details {
    position: absolute;
    display: grid; grid-template-columns: 90px auto;
    row-gap: 12px; font-size: 15px;
  }
  .details dt { color: var(--purple); font-weight: 700; }
  .details dd { color: #222; }
  .details--front { left: 150px; top: 560px; }
  .details--back { left: 110px; top: 560px; }

  /* Footer tab */
  .web-tab {
    position: absolute; bottom: 0; height: 44px;
    background: var(--ink); color: var(--white);
    border-radius: 10px 10px 0 0;
    font-size: 14px; letter-spacing: 0.3px;
    display: flex; align-items: center; justify-content: center;
  }
  .page--front .web-tab { left: 270px; width: 230px; }
  .page--back .web-tab { left: 145px; width: 230px; }
</style>
</head>
<body>
  <main class="spread">
    <section class="page page--back" aria-label="Back cover">
      <div class="band band--thanks">
        <svg viewBox="0 0 520 170" preserveAspectRatio="none" aria-hidden="true">
          <path d="M40 60 Q44 34 72 32 L520 0 L520 170 L110 170 Q80 170 70 140 Z" fill="var(--purple)"/>
        </svg>
        <div class="band__text">Thank You!</div>
      </div>
      <dl class="details details--back">
        <dt>Email:</dt><dd>info@civicanalysisinstitute.org</dd>
        <dt>ISBN:</dt><dd>CHF-467.113.214</dd>
      </dl>
      <div class="web-tab">www.civicanalysisinstitute.org</div>
    </section>

    <section class="page page--front" aria-label="Front cover">
      <header class="brand">
        <div class="brand__name">CIVIC</div>
        <div class="brand__sub">ANALYSIS INSTITUTE</div>
      </header>
      <div class="cover-photo" role="img" aria-label="Photo of business people discussing charts around a meeting table"></div>
      <div class="band band--title">
        <svg viewBox="0 0 400 210" preserveAspectRatio="none" aria-hidden="true">
          <path d="M0 40 Q2 12 30 12 L372 0 Q400 0 400 28 L400 210 L70 210 Q44 210 40 184 Z" fill="var(--purple)"/>
        </svg>
        <h1 class="band__text">Pre-Study for an Impact Evaluation of the ABC programme</h1>
      </div>
      <dl class="details details--front">
        <dt>Client:</dt><dd>ABC Company</dd>
        <dt>Date:</dt><dd>September 22, 2018</dd>
      </dl>
      <div class="web-tab">www.civicanalysisinstitute.org</div>
    </section>
  </main>
</body>
</html>
```